Golden Coat All-Purpose Breading Bag Design

Our client, Halvern Food Products, is looking to re-design the packaging for their product, Pellham's Golden Coat. Goldn Coat is an all-purpose food breading mix.

Halvern Foods has a registered trademark for this product, but they have not been using it for this particular 10 pound bag. They want to get the trademark onto the bag and also give the bag an updated look. They would like to continue to use the same red and blue colors. This 10 pound bag is not available on store shelves; it is sold to food service distributors who sell to restaurants.

All of the copy on the existing bag is still relevant, so we will want to incoprporate it into the bag design. Once these bags are filled with product, the tops get folded over about 1 inch and then sewn shut with thread.

Eventually, we will need the design applied to the Bag Template file attached, but that isn't important until a design is selected.

Target Market(s)

Restaurants

Industry/Entity Type

Food Manufacturing

Colors
0054AA
0677BA
7BADD7
CADEEF
E8F1F8
EB3D1F
EC4F4E
F09395
F8D3D4
FCEDEE

Requirements
Must have
• Trademark introduced to the design

```html
<!DOCTYPE html>
<html lang="en">
<head>
<meta charset="utf-8">
<title>Pellham's Golden Coat – 10 lb Bag</title>
<link href="https://fonts.googleapis.com/css2?family=Nunito:wght@700&family=Barlow:wght@400;600;700&family=Barlow+Semi+Condensed:wght@600&family=Open+Sans:wght@400;700&display=swap" rel="stylesheet">
<style>
  :root {
    --blue-deep: #0b1688;
    --blue-mid: #1c5fb0;
    --blue-light: #2479c1;
    --red-base: #9c160b;
    --red-glow: #b8463c;
    --red-shadow: #5a0a04;
    --white: #ffffff;
  }
  html, body {
    margin: 0;
    width: 1136px;
    height: 1200px;
    overflow: hidden;
    background: var(--white);
  }
  .canvas {
    position: relative;
    width: 1136px;
    height: 1200px;
  }
  .bag {
    position: absolute;
    left: 275px;
    top: 77px;
    width: 968px;
    height: 1724px;
    transform: scale(0.6055);
    transform-origin: top left;
    overflow: hidden;
  }
  .bag-art {
    position: absolute;
    inset: 0;
    width: 968px;
    height: 1724px;
  }
  .tagline {
    position: absolute;
    left: 190px;
    top: 500px;
    width: 600px;
    transform: rotate(-6deg);
    font-family: "Open Sans", sans-serif;
    font-size: 33px;
    line-height: 38px;
    color: var(--white);
    text-align: center;
    margin: 0;
  }
  .tagline strong { font-weight: 700; }
  .brand-lockup {
    position: absolute;
    left: 0;
    top: 700px;
    width: 968px;
    text-align: center;
    font-family: "Nunito", sans-serif;
    font-weight: 700;
    color: var(--white);
  }
  .brand-name {
    font-size: 150px;
    line-height: 160px;
    margin: 0;
  }
  .brand-maker {
    font-size: 52px;
    line-height: 56px;
    margin: -6px 0 0 0;
  }
  .product-name {
    font-size: 150px;
    line-height: 170px;
    letter-spacing: -3px;
    margin: 0;
  }
  .claims {
    position: absolute;
    left: 138px;
    top: 1152px;
    width: 706px;
    height: 168px;
    border: 2px dashed var(--white);
    border-radius: 16px;
    box-sizing: border-box;
    color: var(--white);
  }
  .claims-main {
    height: 102px;
    border-bottom: 2px dashed var(--white);
    display: flex;
    align-items: center;
    justify-content: center;
    font-family: "Barlow Semi Condensed", sans-serif;
    font-weight: 600;
    font-size: 46px;
    letter-spacing: 1px;
    margin: 0;
  }
  .claims-note {
    height: 62px;
    display: flex;
    align-items: center;
    justify-content: center;
    gap: 12px;
    font-family: "Barlow", sans-serif;
    font-size: 27px;
    margin: 0;
  }
  .net-weight {
    position: absolute;
    right: 82px;
    top: 1440px;
    margin: 0;
    font-family: "Barlow", sans-serif;
    font-size: 54px;
    line-height: 60px;
    color: var(--white);
  }
  .net-weight strong { font-weight: 700; }
  .ingredients {
    position: absolute;
    left: 13px;
    top: 1514px;
    width: 420px;
    margin: 0;
    font-family: "Barlow", sans-serif;
    font-size: 23px;
    line-height: 22px;
    color: var(--white);
    text-transform: uppercase;
  }
  .ingredients strong { font-weight: 700; }
</style>
</head>
<body>
<div class="canvas">
  <div class="bag">
    <svg class="bag-art" viewBox="0 0 968 1724" xmlns="http://www.w3.org/2000/svg">
      <defs>
        <linearGradient id="band-blue" x1="0" y1="0" x2="1" y2="0">
          <stop offset="0" stop-color="var(--blue-deep)"/>
          <stop offset="0.3" stop-color="var(--blue-mid)"/>
          <stop offset="0.55" stop-color="var(--blue-light)"/>
          <stop offset="0.8" stop-color="var(--blue-mid)"/>
          <stop offset="1" stop-color="var(--blue-deep)"/>
        </linearGradient>
        <radialGradient id="burst-red" cx="0.5" cy="0.53" r="0.7">
          <stop offset="0" stop-color="var(--red-glow)"/>
          <stop offset="1" stop-color="var(--red-base)"/>
        </radialGradient>
        <filter id="edge-shadow" x="-10%" y="-20%" width="120%" height="140%">
          <feDropShadow dx="0" dy="0" stdDeviation="10" flood-color="var(--red-shadow)" flood-opacity="0.8"/>
        </filter>
      </defs>

      <rect class="burst-field" role="img" aria-label="Red sunburst rays radiating from the centre" x="0" y="0" width="968" height="1724" fill="url(#burst-red)"/>

      <g class="top-band" filter="url(#edge-shadow)">
        <path fill="var(--white)" d="M0 0 H968 V312 C850 345 700 330 550 278 S260 165 0 194 Z"/>
      </g>
      <path class="top-band-blue" fill="url(#band-blue)" d="M0 0 H968 V282 C850 315 700 300 550 250 S260 140 0 172 Z"/>

      <g class="bottom-band" filter="url(#edge-shadow)">
        <path fill="var(--white)" d="M0 1442 C60 1420 120 1415 170 1418 C330 1428 460 1500 600 1560 C680 1592 740 1600 800 1600 C870 1600 930 1585 968 1572 V1724 H0 Z"/>
      </g>
      <path class="bottom-band-blue" fill="url(#band-blue)" d="M0 1470 C60 1448 120 1443 170 1446 C330 1456 460 1526 600 1584 C680 1614 740 1622 800 1622 C870 1622 930 1606 968 1592 V1724 H0 Z"/>

      <path class="tagline-ribbon" fill="url(#band-blue)" d="M148 488 C300 510 500 480 665 465 C760 457 820 470 866 487 C830 498 810 510 800 520 C830 545 855 570 862 593 C800 575 700 575 620 583 C450 600 300 630 136 592 C175 585 195 570 205 555 C180 535 160 510 148 488 Z"/>
    </svg>

    <p class="tagline">Chicken fried the <strong>GOLDEN COAT</strong> way<br>is fried chicken the <strong>right away.</strong></p>

    <div class="brand-lockup">
      <p class="brand-name">Pellham's</p>
      <p class="brand-maker">by Halvern</p>
      <p class="product-name">Golden Coat</p>
    </div>

    <div class="claims">
      <p class="claims-main">SEALS JUICE IN - GREASE OUT</p>
      <p class="claims-note">
        <svg width="30" height="30" viewBox="0 0 30 30" aria-hidden="true">
          <circle cx="15" cy="15" r="12.5" fill="none" stroke="var(--white)" stroke-width="3"/>
          <path d="M15 8 V16 H21" fill="none" stroke="var(--white)" stroke-width="3" stroke-linecap="round"/>
        </svg>
        Cooks two-pound chicken well done in 10 min.
      </p>
    </div>

    <p class="net-weight"><strong>NET WT.</strong> 10 LBS.</p>

    <p class="ingredients"><strong>Ingredients:</strong> Flour, salt, eggs yolk, non-fat milk solids, baking powder, corn starch, sugar and pepper.</p>
  </div>
</div>
</body>
</html>
```